Design my site www.brieflyledger.com

So here is what I am thinking in terms of design:

https://plenvo.com

https://www.skyluxair.com

http://kalvex.com/harbor-plaza-tower/

I want the theme to be white and blue (royal blue). I attached a paint picture of what I would like the site to look like in terms of placing the text. Generally, what I like about the sites above is that they are simple, you can navigate easily and have some kind of idea of what's going on by looking at the center (picture and motto). Let's establish a clear understanding of how the functional part of the site would look like. Please see the picture attached.

I want to keep it simple: On top would be the Name 'BRIEFLY ledger", somewhere to the right on top on the page would be 'Sign in" button.

In the center would be a picture (maybe a video) with the Motto (on top of it all in capital) OBSERVE NAVIGATE DECIDE and below would be the "sign up now"

Below the picture (like on kalvex.com site) or to the left on top of the page would be "About Us', "Press" "Contact Us' buttons.

Then once the user gets to his page his got 3 tabs " Press Headlines", "Events", " Briefings".

we would keep the same format I only have on the site, but separate for every Tab.

I do not want the user to get distracted. I also want him to be able to access the page though mobile phone and be able to get automatic updates just like Zorvan Pings without having to sign in daily.

The landing page must be minimalist yet with business/corporate feel where users can navigate easily and a "what you see is what you get" approach. You want an image or video (personally I prefer the video.. it does capture the users attention instantly, as long as it is an interesting video), with your taglines in it.

Sections available to public: About Us, Contact Us, Landing Page with Signup Option

Private: Public Sections + User Account Page, Tabs for (Events, Press Headlines, Briefings)

Target Market(s)

PR/media monitoring/diplomatic community

Coding

Coded - Design and coding required

Number of Pages Required

1 page

Font styles to use
Serif
Sans Serif

Colors
0255a3
ec1f27

Requirements
Must have
• a simple landing page, that is user friendly.
Nice to have
• a video with the explanation of how to navigate the site
Should not have
• too many colors, graphs etc.

```html
<!DOCTYPE html>
<html lang="en">
<head>
<meta charset="utf-8">
<title>Briefly Ledger</title>
<link href="https://fonts.googleapis.com/css2?family=Inter:wght@300;400;600;700;800&display=swap" rel="stylesheet">
<style>
  :root {
    --royal: #0255a3;
    --brand-blue: #1a4f9c;
    --accent: #ec1f7a;
    --nav-blue: #2a83dc;
    --nav-press: #a5004f;
    --white: #ffffff;
    --bar-grey: #f2f3f5;
    --line-grey: #e1e3e8;
    --social: #2e5f9e;
  }
  * { box-sizing: border-box; margin: 0; padding: 0; }
  html, body { width: 1200px; height: 716px; overflow: hidden; background: var(--white); }
  body { font-family: "Inter", Arial, sans-serif; color: var(--white); }

  .site { position: relative; width: 1200px; height: 716px; }

  .topbar {
    position: absolute; left: 0; top: 0; width: 1200px; height: 61px;
    background: var(--white); display: flex; align-items: center;
  }
  .brand {
    margin-left: 30px; font-size: 21px; font-weight: 700; letter-spacing: 0.2px;
    color: var(--brand-blue);
  }
  .brand-accent { color: var(--accent); }
  .social {
    margin-left: auto; height: 61px; width: 190px; background: var(--bar-grey);
    border-left: 1px solid var(--line-grey);
    display: flex; align-items: center; justify-content: center; gap: 2px;
  }
  .social-link {
    width: 32px; height: 30px; background: var(--social); color: var(--white);
    font-size: 7.5px; font-weight: 600; display: flex; align-items: center; justify-content: center;
    text-decoration: none;
  }
  .sign-in {
    width: 128px; height: 61px; background: var(--royal); color: var(--white);
    font-size: 14px; font-weight: 700; display: flex; align-items: center; justify-content: center;
    text-decoration: none; letter-spacing: 0.3px;
  }

  .hero {
    position: absolute; left: 0; top: 61px; width: 1200px; height: 594px;
    background:
      linear-gradient(rgba(28,26,40,0.55), rgba(28,26,40,0.55)),
      linear-gradient(160deg, #4b4a52 0%, #6e6558 35%, #3d3f4a 60%, #5a5650 80%, #2f313a 100%);
  }
  .hero-content {
    position: absolute; left: 0; top: 0; width: 100%; height: 100%;
    display: flex; flex-direction: column; align-items: center;
  }
  .hero-mark { margin-top: 160px; width: 62px; height: 62px; }
  .hero-title {
    margin-top: 26px; display: flex; align-items: center; gap: 14px;
    font-size: 63px; font-weight: 800; letter-spacing: 1px; line-height: 1;
  }
  .hero-rule { width: 102px; height: 2px; background: var(--accent); }
  .hero-motto { margin-top: 22px; font-size: 28px; font-weight: 300; letter-spacing: 0.2px; }
  .cta {
    margin-top: 28px; width: 229px; height: 49px; border: 1px solid rgba(255,255,255,0.7);
    display: flex; align-items: center; justify-content: center;
    color: var(--white); font-size: 18px; font-weight: 700; text-decoration: none; letter-spacing: 0.3px;
  }

  .section-nav {
    position: absolute; left: 0; top: 655px; width: 1200px; height: 61px; display: flex;
  }
  .section-link {
    flex: 1; display: flex; align-items: center; justify-content: center; gap: 16px;
    background: var(--nav-blue); color: var(--white); text-decoration: none;
    font-size: 19px; font-weight: 700; letter-spacing: 0.3px;
  }
  .section-link + .section-link { border-left: 1px solid rgba(0,0,0,0.25); }
  .section-link.is-active { background: radial-gradient(circle at 50% 60%, #c0035e, var(--nav-press)); }
  .section-icon { width: 32px; height: 32px; }
</style>
</head>
<body>
<div class="site">
  <header class="topbar">
    <div class="brand">BRIEFLY <span class="brand-accent">LEDGER</span></div>
    <nav class="social" aria-label="Social">
      <a class="social-link" href="#">Vizo</a>
      <a class="social-link" href="#">Snapla</a>
      <a class="social-link" href="#">Rello</a>
      <a class="social-link" href="#">Circly</a>
      <a class="social-link" href="#">Workby</a>
    </nav>
    <a class="sign-in" href="#">SIGN IN</a>
  </header>

  <section class="hero">
    <div class="hero-backdrop" role="img" aria-label="Aerial photograph of a dense downtown skyline with office towers"></div>
    <div class="hero-content">
      <svg class="hero-mark" viewBox="0 0 62 62" aria-hidden="true">
        <rect x="4" y="4" width="54" height="54" rx="6" fill="none" stroke="#ffffff" stroke-width="4"/>
      </svg>
      <h1 class="hero-title"><span class="hero-rule"></span>BRIEFLY LEDGER<span class="hero-rule"></span></h1>
      <p class="hero-motto">OBSERVE • NAVIGATE • DECIDE</p>
      <a class="cta" href="#">SIGN UP NOW</a>
    </div>
  </section>

  <nav class="section-nav" aria-label="Sections">
    <a class="section-link" href="#">
      <svg class="section-icon" viewBox="0 0 32 32" fill="none" stroke="#fff" stroke-width="2">
        <circle cx="16" cy="16" r="14.5"/>
        <circle cx="16" cy="12.5" r="5"/>
        <path d="M7 26c1.5-5 5-7 9-7s7.5 2 9 7"/>
      </svg>
      ABOUT US
    </a>
    <a class="section-link is-active" href="#">
      <svg class="section-icon" viewBox="0 0 36 28" fill="none" stroke="#fff" stroke-width="2">
        <rect x="5" y="2" width="29" height="24" rx="2"/>
        <path d="M5 8H2v15a3 3 0 0 0 6 0"/>
        <rect x="9" y="6" width="21" height="5" fill="#fff"/>
        <path d="M9 15h9M9 19h9M9 23h9M21 15h9v8h-9z"/>
      </svg>
      PRESS
    </a>
    <a class="section-link" href="#">
      <svg class="section-icon" viewBox="0 0 32 32" fill="none" stroke="#fff" stroke-width="2">
        <rect x="4" y="2" width="24" height="28"/>
        <path d="M8 2v28" />
        <circle cx="18" cy="13" r="4" fill="#fff"/>
        <path d="M11 25c1-4 4-6 7-6s6 2 7 6z" fill="#fff"/>
      </svg>
      CONTACT US
    </a>
  </nav>
</div>
</body>
</html>
```